Modern design company business card design

We are a design oriented construction firm. The owner is an architect and licensed General Contractor and accomplished furniture designer. We do new home construction and large scale remodeling and office design. We would like a design for our new business cards that is clean and modern, but relatable. We like the bright green color of our logo mixed with different shades of grey. We're also open to reinterpreting the logo.

Target Market(s)

Potential design clients,
Construction clients

Industry/Entity Type

Architecture

Contact Information for Business Card

Tall Maple Design | Build Inc. (optional with logo, Inc. optional)Jeffrey MorganOwner (optional)317.555.0148 cell317.431.8056 officejmorgan@greensquareinc.comwww.greensquareinc.com

Font styles to use
Sans Serif
Other font styles liked:
• Avenir

Requirements
Nice to have
• I like designs that have some continuity between the front and back, i.e. similar layouts or graphic elements that wrap around the card. I tend to prefer horizontal over vertical, but that's not a have to. I also tend to prefer white or recycled paper.

```html
<!DOCTYPE html>
<html lang="en">
<head>
<meta charset="utf-8">
<title>Tall Maple Design | Build – Business Cards</title>
<link rel="stylesheet" href="https://fonts.googleapis.com/css2?family=Open+Sans:wght@400;600;700&display=swap">
<style>
  :root {
    --page-bg: #e9e7e3;
    --slate: #55585c;
    --slate-dark: #3a3c40;
    --slate-light: #808387;
    --ink: #5b5e62;
    --paper: #ffffff;
    --green: #2ea84a;
  }
  * { box-sizing: border-box; margin: 0; padding: 0; }
  html, body {
    width: 1200px; height: 913px; overflow: hidden;
    background: var(--page-bg);
    font-family: "Open Sans", Arial, sans-serif;
  }
  .canvas { position: relative; width: 1200px; height: 913px; }

  .card {
    position: absolute;
    width: 560px; height: 320px;
    padding: 12px;
    box-shadow: 0 12px 30px rgba(0,0,0,.18);
  }
  .card-front { left: 80px; top: 120px; background: var(--slate); }
  .card-back  { left: 560px; top: 480px; background: var(--green); }

  .card-face { position: relative; width: 100%; height: 100%; overflow: hidden; }
  .card-front .card-face { background: var(--paper); }
  .card-back .card-face {
    background: linear-gradient(160deg, var(--slate-light) 0%, var(--slate) 55%, var(--slate-dark) 100%);
  }

  /* Company name set as plain text, one colour and one weight */
  .brand-name {
    position: absolute;
    font-weight: 600;
    text-transform: uppercase;
    line-height: 1.1;
    letter-spacing: .06em;
  }
  .brand-name span { display: block; }
  .brand-name .brand-main { font-size: 26px; }
  .brand-name .brand-sub { font-size: 14px; letter-spacing: .14em; margin-top: 2px; }

  .card-front .brand-name { left: 22px; bottom: 26px; color: var(--ink); }
  .card-back .brand-name {
    left: 0; right: 0; top: 50%; transform: translateY(-50%);
    text-align: center; color: var(--paper);
  }
  .card-back .brand-name .brand-main { font-size: 34px; }
  .card-back .brand-name .brand-sub { font-size: 17px; margin-top: 4px; }

  .person-name {
    position: absolute; right: 18px; top: 84px;
    font-size: 17px; font-weight: 700; color: var(--ink);
    letter-spacing: .03em; text-transform: uppercase;
  }
  .divider {
    position: absolute; left: 22px; right: 16px; top: 112px;
    height: 1.5px; background: var(--ink);
  }
  .person-role {
    position: absolute; right: 18px; top: 117px;
    font-size: 11px; color: var(--green); letter-spacing: .06em;
  }
  .contact-list {
    position: absolute; right: 18px; top: 140px;
    list-style: none; text-align: right;
    font-size: 12.5px; color: var(--ink); line-height: 19px;
  }
  .contact-list li { display: flex; justify-content: flex-end; align-items: center; gap: 6px; }
  .contact-list svg { width: 11px; height: 11px; flex: none; }
  .icon-line { fill: none; stroke: var(--green); stroke-width: 1.6; }
</style>
</head>
<body>
<main class="canvas">

  <section class="card card-front" aria-label="Card front">
    <div class="card-face">
      <div class="person-name">Dennis Holloway</div>
      <div class="divider"></div>
      <div class="person-role">OWNER</div>
      <ul class="contact-list">
        <li>317.555.0172
          <svg viewBox="0 0 12 12" aria-hidden="true"><rect class="icon-line" x="3" y="1" width="6" height="10" rx="1"/></svg>
        </li>
        <li>317.555.0148
          <svg viewBox="0 0 12 12" aria-hidden="true"><path class="icon-line" d="M2 2 L4.5 1.5 L5.5 4 L4 5 Q5 7.5 7 8 L8 6.5 L10.5 7.5 L10 10 Q4 10.5 2 2 Z"/></svg>
        </li>
        <li>www.tallmapleinc.example
          <svg viewBox="0 0 12 12" aria-hidden="true"><circle class="icon-line" cx="6" cy="6" r="4.8"/><path class="icon-line" d="M1.2 6 H10.8 M6 1.2 Q3 6 6 10.8 Q9 6 6 1.2"/></svg>
        </li>
        <li>dholloway@tallmapleinc.example
          <svg viewBox="0 0 12 12" aria-hidden="true"><rect class="icon-line" x="1" y="2.5" width="10" height="7"/><path class="icon-line" d="M1 2.5 L6 6.5 L11 2.5"/></svg>
        </li>
      </ul>
      <div class="brand-name">
        <span class="brand-main">Tall Maple</span>
        <span class="brand-sub">Design | Build</span>
      </div>
    </div>
  </section>

  <section class="card card-back" aria-label="Card back">
    <div class="card-face">
      <div class="brand-name">
        <span class="brand-main">Tall Maple</span>
        <span class="brand-sub">Design | Build</span>
      </div>
    </div>
  </section>

</main>
</body>
</html>
```